Business Card Design

We are a law firm which provides services to creditors.....we do collection litigation. I am wide open on suggestions. I was thinking of a square card? Alternatively, a vertically oriented standard card or a folded card.....something unique. I would like to use my firm logo and beyond that, I am open for any and all suggestions. I'm uncertain if the complete log is uploaded? If not, please let me email it to you.

Industry/Entity Type

Law Firm

Contact Information for Business Card

Hart, Crane & Dobbs, P.C.
Tom Dobbs, Lawyer
4387 N Larkspur Ave
Oklahoma City, OK 73924
tdobbs@HcdCounsel.com
www.HcdCounsel.com
mobile: 405-382-7914

```html
<!DOCTYPE html>
<html lang="en">
<head>
<meta charset="utf-8">
<title>Hart, Crane &amp; Dobbs, P.C. — Business Card</title>
<link rel="stylesheet" href="https://fonts.googleapis.com/css2?family=Roboto:wght@400;500;700&display=swap">
<style>
  :root {
    --green: #17924a;
    --green-dark: #0f7a3c;
    --gold: #c9a43a;
    --ink: #3a3a3a;
    --grey-text: #555555;
    --card: #ffffff;
    --bg: #e9e9e7;
  }
  * { box-sizing: border-box; margin: 0; padding: 0; }
  html, body { width: 1200px; height: 885px; overflow: hidden; }
  body {
    background: var(--bg);
    font-family: "Roboto", Arial, sans-serif;
    position: relative;
  }
  .card {
    position: absolute;
    width: 640px;
    height: 366px;
    background: var(--card);
    box-shadow: 0 2px 10px rgba(0,0,0,0.12);
    overflow: hidden;
  }
  .card-front { left: 280px; top: 58px; }
  .card-back  { left: 280px; top: 462px; }

  /* front */
  .mark {
    position: absolute;
    display: flex;
    align-items: center;
    gap: 10px;
  }
  .mark-dot {
    width: 26px; height: 26px;
    border-radius: 50%;
    background: var(--green);
    flex: none;
  }
  .mark-name {
    color: var(--green);
    font-weight: 700;
    font-size: 17px;
    line-height: 1.2;
  }
  .card-front .mark { left: 30px; top: 140px; width: 210px; }

  .divider {
    position: absolute;
    left: 262px; top: 34px;
    width: 1px; height: 230px;
    background: var(--green);
  }
  .holder { position: absolute; left: 300px; top: 46px; }
  .holder-name {
    color: var(--green);
    font-weight: 700;
    font-size: 42px;
    line-height: 1;
  }
  .holder-title {
    color: var(--ink);
    font-weight: 700;
    font-size: 25px;
    margin-top: 4px;
  }
  .contacts {
    position: absolute;
    left: 300px; top: 178px;
    list-style: none;
    font-size: 16px;
    color: var(--grey-text);
  }
  .contacts li { display: flex; align-items: center; gap: 9px; height: 24px; }
  .contact-icon { width: 15px; height: 15px; flex: none; }

  .address-band {
    position: absolute;
    left: 0; right: 0; bottom: 0;
    height: 64px;
    background: linear-gradient(var(--green), var(--green-dark));
    border-top: 3px solid var(--gold);
    display: flex; align-items: center; justify-content: center;
    color: #fff;
    font-weight: 700;
    font-size: 24px;
    letter-spacing: 0.2px;
  }

  /* back */
  .card-back .mark {
    left: 0; right: 0; top: 110px;
    justify-content: center;
  }
  .firm-name {
    position: absolute;
    left: 0; right: 0; top: 214px;
    text-align: center;
    color: var(--green);
    font-weight: 700;
    font-size: 38px;
  }
</style>
</head>
<body>

<section class="card card-front" aria-label="Business card front">
  <div class="mark">
    <span class="mark-dot"></span>
    <span class="mark-name">Hart, Crane &amp; Dobbs, P.C.</span>
  </div>
  <div class="divider"></div>
  <div class="holder">
    <p class="holder-name">Tom Dobbs</p>
    <p class="holder-title">Lawyer</p>
  </div>
  <ul class="contacts">
    <li>
      <svg class="contact-icon" viewBox="0 0 15 15" aria-hidden="true"><rect width="15" height="15" fill="#17924a"/><rect x="5" y="3" width="5" height="9" rx="1" fill="none" stroke="#fff" stroke-width="1.3"/></svg>
      405-382-7914
    </li>
    <li>
      <svg class="contact-icon" viewBox="0 0 15 15" aria-hidden="true"><rect width="15" height="15" fill="#17924a"/><rect x="3" y="4.5" width="9" height="6" fill="none" stroke="#fff" stroke-width="1.2"/><path d="M3 4.5 7.5 8 12 4.5" fill="none" stroke="#fff" stroke-width="1.2"/></svg>
      tdobbs@HcdCounsel.com
    </li>
    <li>
      <svg class="contact-icon" viewBox="0 0 15 15" aria-hidden="true"><rect width="15" height="15" fill="#17924a"/><circle cx="7.5" cy="7.5" r="4.3" fill="none" stroke="#fff" stroke-width="1.2"/><path d="M3.2 7.5h8.6M7.5 3.2c-2 2.5-2 6.1 0 8.6M7.5 3.2c2 2.5 2 6.1 0 8.6" fill="none" stroke="#fff" stroke-width="1"/></svg>
      www.HcdCounsel.com
    </li>
  </ul>
  <div class="address-band">4387 N Larkspur Ave Oklahoma City, OK 73924</div>
</section>

<section class="card card-back" aria-label="Business card back">
  <div class="mark">
    <span class="mark-dot"></span>
    <span class="mark-name">Hart, Crane &amp; Dobbs, P.C.</span>
  </div>
  <p class="firm-name">Hart, Crane &amp; Dobbs, P.C.</p>
</section>

</body>
</html>
```